Business Card for a Dental Office

The design should communicate integrity, quality and reliability. We also want the card look elegant, simple, but still stand out, different from the traditional-dental-office business card.

Industry/Entity Type

Business

```html
<!DOCTYPE html>
<html lang="en">
<head>
<meta charset="utf-8">
<title>Harwell Dental Studio – Business Card</title>
<link rel="stylesheet" href="https://fonts.googleapis.com/css2?family=Oswald:wght@700&family=Open+Sans:wght@400;700&display=swap">
<style>
  :root {
    --backdrop: #ecebe8;
    --yellow-light: #f7ee3a;
    --yellow-mid: #ece21e;
    --yellow-deep: #d6c40e;
    --ink: #111111;
    --gold: #c9a227;
    --paper: #ffffff;
    --muted: #222222;
  }
  * { margin: 0; padding: 0; box-sizing: border-box; }
  html, body { width: 1200px; height: 900px; overflow: hidden; }
  body {
    background: var(--backdrop);
    position: relative;
    font-family: "Open Sans", Arial, sans-serif;
  }
  .card {
    position: absolute;
    width: 560px;
    height: 320px;
    box-shadow: 0 6px 22px rgba(0,0,0,0.18);
    overflow: hidden;
  }
  .card-front {
    left: 90px;
    top: 110px;
    background: linear-gradient(160deg, var(--yellow-deep) 0%, var(--yellow-light) 45%, var(--yellow-mid) 75%, var(--yellow-deep) 100%);
  }
  .front-brand {
    position: absolute;
    left: 0; right: 0;
    bottom: 58px;
    text-align: center;
  }
  .front-name {
    font-family: "Oswald", "Arial Narrow", sans-serif;
    font-weight: 700;
    font-size: 38px;
    line-height: 1;
    color: var(--ink);
    letter-spacing: 0.5px;
    text-transform: uppercase;
  }
  .front-tagline {
    margin-top: 10px;
    font-weight: 400;
    font-size: 14px;
    letter-spacing: 1px;
    color: var(--ink);
  }
  .card-back {
    left: 550px;
    top: 470px;
    background: var(--paper);
  }
  .contact {
    position: absolute;
    left: 300px;
    top: 34px;
    color: var(--muted);
  }
  .contact-name {
    font-weight: 700;
    font-size: 19px;
    color: var(--gold);
    line-height: 1.1;
  }
  .contact-role { font-size: 13px; margin-top: 2px; }
  .contact-address { margin-top: 14px; font-size: 13.5px; line-height: 1.4; }
  .contact-list { list-style: none; margin-top: 12px; font-size: 13.5px; line-height: 1.45; }
  .contact-list li { display: flex; align-items: center; gap: 10px; }
  .contact-list svg { width: 12px; height: 12px; flex: none; }
  .back-brand {
    position: absolute;
    left: 30px;
    bottom: 40px;
    display: flex;
    align-items: center;
    gap: 12px;
  }
  .brand-square { width: 40px; height: 40px; background: var(--gold); }
  .back-name {
    font-family: "Oswald", "Arial Narrow", sans-serif;
    font-weight: 700;
    font-size: 27px;
    line-height: 1;
    color: var(--ink);
    text-transform: uppercase;
  }
</style>
</head>
<body>

  <section class="card card-front" aria-label="Card front">
    <div class="front-brand">
      <p class="front-name">Harwell Dental Studio</p>
      <p class="front-tagline">Gentle care for every family smile</p>
    </div>
  </section>

  <section class="card card-back" aria-label="Card back">
    <div class="contact">
      <p class="contact-name">Daniel Carter</p>
      <p class="contact-role">Managing Director</p>
      <p class="contact-address">12345, Address Goes Here<br>Country Name, 123456.</p>
      <ul class="contact-list">
        <li>
          <svg viewBox="0 0 24 24" aria-hidden="true"><path fill="#c9a227" d="M6.6 10.8a15.1 15.1 0 0 0 6.6 6.6l2.2-2.2a1 1 0 0 1 1-.25 11.4 11.4 0 0 0 3.6.57 1 1 0 0 1 1 1V20a1 1 0 0 1-1 1A17 17 0 0 1 3 4a1 1 0 0 1 1-1h3.5a1 1 0 0 1 1 1c0 1.25.2 2.45.57 3.6a1 1 0 0 1-.25 1z"/></svg>
          <span>044-555 018 240</span>
        </li>
        <li>
          <svg viewBox="0 0 24 24" aria-hidden="true"><path fill="#c9a227" d="M2 5h20v14H2z"/><path fill="none" stroke="#fff" stroke-width="2" d="M2 5l10 8 10-8"/></svg>
          <span>hello@harwellstudio.com</span>
        </li>
        <li>
          <svg viewBox="0 0 24 24" aria-hidden="true"><g fill="none" stroke="#c9a227" stroke-width="3" stroke-linecap="round"><path d="M10 14a4 4 0 0 0 5.7 0l3.6-3.6a4 4 0 0 0-5.7-5.7l-1.2 1.2"/><path d="M14 10a4 4 0 0 0-5.7 0l-3.6 3.6a4 4 0 0 0 5.7 5.7l1.2-1.2"/></g></svg>
          <span>www.harwellstudio.com</span>
        </li>
      </ul>
    </div>

    <div class="back-brand">
      <span class="brand-square" aria-hidden="true"></span>
      <p class="back-name">Harwell Dental Studio</p>
    </div>
  </section>

</body>
</html>
```